Creative Web Design for an ERP (technology) Consulting Business

I need two pages designed for the ERP Project Management Consulting Company I am starting. One page is the home page, the other page is an important inside page.

I've looked at many different templates for sites like this, and they all look the same to me. I am working with PixelGuild designers because I want something unique.

This site will be implemented with Wordpress using the Elementor framework,

About Me ---
I have worked with PixelGuild several times before, and I have tired to do everything I can to ve helpful. In the uploads, you will find PDF's with wireframes outlning the layout of the pages, as well as explanatios for each section. There are Word documents that you can copy into text. The list below explains the files included.

Although the wireframes suggest a layout, please feel free to use your creativity - often, I find that the designs I like the most are designs I have never thought of.

About the Company --
ERP (Enterprise Resource Planning) systems are business computer systems that tie different businesss functions together. These systems are expensive and complicated, and efforts to implement them often fail. The purpose of the company is to increase the chance of success by focusing on the things that need to be right.

I have uploaded several files to help clarify what I am looking for:
• 1a - Home Page Wireframe - PDF
Wireframe for the home page with an explanation of each section.
• 1b - Home Page Text – Word
A Word document so that you can copy the text.
• 2 - Copper Harbor Logo – ZIP
Four different versions of the company logo in Adobe Illustrator, PNG, and JPG formats. Any of the four are acceptable:
1. Logo_1 – Black on Transparent – Same Line ERP
2. Logo_2 – White on Transparent – Same Line ERP
3. Logo_3 – Black on Transparent – Big ERP on Different Line
4. Logo_4 – White on Transparent – Big ERP on Different Line
• 3a - Copper Harbor Page Wireframe – PDF
Wireframe for he Copper Harbor page, with explanations and a detailed breakdown of the top section.
• 3b - Copper Harbor Text – Word
• 4 - Colors and Palettes – PDF
• 5 - Change Management Icon – EPS
• 6 – Site Map
If you wish to see it, the site map provides an idea of the entire site. The two pages circled in red are the ones I need to be designed.

Thank you for your interest in this project!

Target Market(s)

Corporate decision makers, primarily CIOs and CFOs, as well as ERP project managers and influencers.

Industry/Entity Type

Consulting

Number of Pages Required

2 page

Font styles to use
Sans Serif

Requirements
Must have
• Pages that contain the elements explained on the wireframes provided.
Nice to have
• A design that looks and feels unique
Should not have
• A typical, template layour

```html
<!DOCTYPE html>
<html lang="en">
<head>
<meta charset="utf-8">
<title>Copper Harbor ERP — Home</title>
<link href="https://fonts.googleapis.com/css2?family=Montserrat:wght@500;600;700&family=Roboto:wght@400;500;700&display=swap" rel="stylesheet">
<style>
:root{
  --orange:#f47a20;
  --red:#e8402c;
  --ink:#1d1d1f;
  --text:#333;
  --muted:#555;
  --blue:#0b5cc7;
  --lavender:#7a8acb;
  --green:#2aa14b;
  --teal:#3ca57c;
  --card:#f2f1f3;
  --pale:#f7f7f8;
  --footer:#1c1c1c;
  --purple:#5b2d8c;
}
*{box-sizing:border-box;margin:0;padding:0}
html,body{width:1200px;height:4819px;overflow:hidden}
body{position:relative;background:#fff;font-family:"Roboto",Arial,sans-serif;color:var(--text)}
.abs{position:absolute}
h1,h2,h3,.heading{font-family:"Montserrat",Arial,sans-serif;color:var(--ink)}
.btn{display:inline-block;background:var(--orange);color:#fff;font-family:"Montserrat",Arial,sans-serif;font-weight:600;font-size:15px;border-radius:22px;padding:11px 22px;white-space:nowrap}
.photo{border-radius:10px}
.brand-dot{display:inline-block;width:14px;height:14px;border-radius:50%;background:var(--orange);vertical-align:middle;margin-right:10px}

/* header */
.site-header{left:0;top:0;width:1200px;height:100px;background:#fff}
.logo{left:150px;top:30px;font-family:"Montserrat",sans-serif;font-weight:700;font-size:20px;color:var(--ink)}
.logo small{display:block;font-size:9px;font-weight:500;letter-spacing:2px;color:var(--muted);margin-left:24px;margin-top:2px}
.nav{left:413px;top:32px;display:flex;font-size:13px}
.nav a{color:var(--ink);text-decoration:none;padding:8px 12px}
.nav a.active{background:var(--red);color:#fff;border-radius:16px}

/* hero */
.hero{left:0;top:100px;width:1200px;height:518px;background:linear-gradient(90deg,#6f8197 0%,#9fb0c0 40%,#dfe5ea 58%,#f4f6f8 70%,#f8f9fa 100%)}
.hero-copy{left:714px;top:40px;width:360px}
.hero-copy h1{font-size:24px;line-height:30px;font-weight:600}
.hero-tag{display:inline-block;margin-top:20px;background:#fff;border-radius:16px;padding:7px 12px;font-size:14px;box-shadow:0 2px 6px rgba(0,0,0,.08)}
.hero-list{list-style:none;margin-top:16px;font-size:14px}
.hero-list li{margin-bottom:17px;padding-left:24px;position:relative}
.hero-list li:before{content:"";position:absolute;left:2px;top:4px;width:8px;height:8px;border-radius:50%;background:var(--purple)}
.hero-copy .btn{background:var(--red);padding:11px 30px;margin-top:1px}

/* section titles */
.sec-title{width:1200px;text-align:center}
.sec-title .mark{display:block;margin:0 auto 18px;width:18px;height:18px;border-radius:50%;background:var(--orange)}
.sec-title h2{font-size:30px;font-weight:600}
.sec-title .rule{display:block;margin:18px auto 0;width:40px;height:3px;background:var(--ink)}

/* about */
.about-bg{left:0;top:618px;width:1200px;height:700px;background:linear-gradient(180deg,#f3f3f4,#fff 60%)}
.about-intro{left:0;top:785px;width:1200px;text-align:center;font-size:14px;line-height:24px}
.info-card{left:148px;width:415px;background:var(--card);border-radius:10px}
.info-card .icon{position:absolute;left:32px;width:74px;height:74px;border-radius:50%;background:var(--orange)}
.info-card .icon svg{position:absolute;left:22px;top:22px}
.info-card h3{position:absolute;left:138px;font-size:16px;font-weight:600}
.info-card p{position:absolute;left:138px;width:250px;font-size:11.5px;line-height:18px;color:var(--text)}

/* framework + method */
.band-method{left:0;top:1780px;width:1200px;height:582px;background:var(--lavender);border-radius:0 0 140px 0}
.band-framework{left:0;top:1360px;width:1200px;height:495px;background:var(--blue);border-radius:140px 0 140px 0}
.band-copy{color:#fff}
.band-copy h2{color:#fff;font-size:29px;line-height:36px;font-weight:600}
.band-copy .rule{display:block;width:56px;height:3px;background:#fff;margin:22px 0 28px}
.band-copy p{font-size:14px;line-height:24px;margin-bottom:24px}

/* services */
.tabs{left:150px;top:2615px;display:flex;gap:14px}
.tab{width:214px;height:78px;border:1px solid #d8d8d8;border-radius:39px;display:flex;align-items:center;padding-left:18px;gap:20px;font-family:"Montserrat",sans-serif;font-weight:600;font-size:14px;line-height:17px;color:var(--ink);background:#fff}
.tab .dot{width:52px;height:52px;border-radius:50%;flex:none}
.tab.active{background:var(--green);border-color:var(--green);color:#fff}
.service-copy{left:686px;top:2755px;width:360px}
.service-copy h2{font-size:30px;line-height:40px;font-weight:600}
.quote{border-left:3px solid var(--green);padding-left:20px;margin-top:26px}
.quote p{color:var(--purple);font-size:15px;line-height:22px}
.quote cite{display:block;font-size:12px;font-style:italic;margin-top:6px;color:var(--text)}
.service-copy .body{font-size:14px;line-height:23px;margin-top:34px}

/* experience */
.experience-bg{left:0;top:3300px;width:1200px;height:900px;background:var(--pale)}
.slide{top:3560px;height:310px;background:linear-gradient(180deg,#7f8c96,#4b5863);border-radius:10px}
.slider-track{left:150px;top:4032px;width:908px;height:5px;background:#2d2f3a;border-radius:3px}
.slider-fill{left:150px;top:4032px;width:148px;height:5px;background:var(--green)}
.slider-knob{left:286px;top:4022px;width:24px;height:24px;border-radius:50%;background:#fff;border:4px solid var(--green)}

/* subscribe */
.subscribe{left:0;top:4090px;width:1200px;height:470px;background:var(--teal);border-radius:0 140px 0 0}
.subscribe h2{position:absolute;left:0;top:120px;width:1200px;text-align:center;color:#fff;font-size:44px;font-weight:600}
.email-field{left:247px;top:4302px;width:706px;height:54px;background:#fff;border-radius:27px}
.email-label{position:absolute;left:68px;top:18px;font-size:14px;color:var(--ink)}
.email-submit{position:absolute;right:16px;top:8px;padding:10px 22px;font-size:15px}

/* footer */
.footer{left:0;top:4460px;width:1200px;height:359px;background:var(--footer);border-radius:120px 0 0 0;color:#cfcfcf}
.footer-logo{left:148px;top:92px;font-family:"Montserrat",sans-serif;font-weight:600;font-size:23px;color:#fff}
.footer-logo small{display:block;font-size:11px;letter-spacing:3px;margin-top:2px;color:#cfcfcf;font-weight:500}
.f-col{top:62px;font-size:13px;line-height:22px}
.f-col h4{color:#fff;font-family:"Montserrat",sans-serif;font-weight:600;font-size:16px;margin-bottom:12px}
.f-col .row{display:flex;align-items:center;gap:10px;margin-bottom:8px}
.copyright{left:0;top:310px;width:1200px;text-align:center;font-size:11px;color:#cfcfcf}
</style>
</head>
<body>

<header class="site-header abs">
  <div class="logo abs"><span class="brand-dot"></span>COPPER HARBOR ERP<small>BUILT FOR ERP SUCCESS</small></div>
  <nav class="nav abs">
    <a class="active">Home</a><a>About</a><a>Services</a><a>Framework</a><a>Wayfinder</a><a>Resources</a><a>Case Studies</a><a>Contact</a>
  </nav>
</header>

<section class="hero abs" role="img" aria-label="Photo of three consultants reviewing a laptop in a bright office">
  <div class="hero-copy abs">
    <h1>Decades in pursuit of excellence in enterprise applications informed by a researched approach to ERP success.</h1>
    <span class="hero-tag">We can help you with ERP</span>
    <ul class="hero-list">
      <li>Project Planning</li>
      <li>Project Management</li>
      <li>Project Assessments and Turnaround</li>
      <li>Change Management</li>
    </ul>
    <span class="btn">Contact</span>
  </div>
</section>

<div class="about-bg abs"></div>
<div class="sec-title abs" style="top:670px"><span class="mark"></span><h2>ABOUT</h2></div>
<p class="about-intro abs">Hi! I'm Daniel Marsh, a consultant and ERP leader with extensive experience in ERP project management.<br>My journey is shaped by experience, lifelong learning, and a commitment to excellence.</p>

<div class="info-card abs" style="top:876px;height:170px">
  <div class="icon" style="top:40px"><svg width="30" height="30" viewBox="0 0 30 30"><path d="M6 2h12l6 6v20H6z" fill="#fff"/><path d="M10 14h10M10 19h10M10 24h6" stroke="#f47a20" stroke-width="2"/></svg></div>
  <h3 style="top:32px">Looking for Information?</h3>
  <p style="top:64px">This site shares information related to successful ERP implementations within a framework and method based on "whys."</p>
</div>
<div class="info-card abs" style="top:1060px;height:230px">
  <div class="icon" style="top:40px"><svg width="30" height="30" viewBox="0 0 30 30"><path d="M15 27 3 15a7 7 0 0 1 12-9 7 7 0 0 1 12 9z" fill="#fff"/></svg></div>
  <h3 style="top:32px">Looking for help?</h3>
  <p style="top:64px">My purpose is to help organizations maximize the transformational value of ERP systems while minimizing organizational pain and damage. My approach is the result of years of research into what it takes to be successful in ERP implementations, supported by real-world experience.</p>
</div>
<div class="photo abs" style="left:588px;top:876px;width:466px;height:412px;background:linear-gradient(135deg,#c9ccd1,#8f98a3)" role="img" aria-label="Video thumbnail of a team discussing charts around a table">
  <svg class="abs" style="left:203px;top:176px" width="60" height="60" viewBox="0 0 60 60"><circle cx="30" cy="30" r="30" fill="#f47a20"/><path d="M24 18l18 12-18 12z" fill="#fff"/></svg>
</div>

<div class="band-method abs"></div>
<section class="band-framework abs">
  <div class="photo abs" style="left:150px;top:62px;width:433px;height:376px;background:linear-gradient(135deg,#9a9a98,#5d5f61)" role="img" aria-label="Video thumbnail of a team meeting at a round table seen from above">
    <svg class="abs" style="left:186px;top:158px" width="60" height="60" viewBox="0 0 60 60"><circle cx="30" cy="30" r="30" fill="#f47a20"/><path d="M24 18l18 12-18 12z" fill="#fff"/></svg>
  </div>
  <div class="band-copy abs" style="left:632px;top:60px;width:420px">
    <h2>COPPER HARBOR<br>ERP FRAMEWORK</h2>
    <span class="rule"></span>
    <p>The number of things you need to do in an ERP implementation boggles the mind.</p>
    <p>It starts with 'why.' Copper Harbor groups hundreds of critical success factors into recurring themes, distilling them into high-level categories that drive success. Copper Harbor simplifies complexity while retaining essential details.</p>
    <span class="btn">Read More</span>
  </div>
</section>
<section class="abs" style="left:0;top:1855px;width:1200px;height:507px">
  <div class="band-copy abs" style="left:163px;top:80px;width:410px">
    <h2>WAYFINDER METHOD</h2>
    <span class="rule"></span>
    <p>The framework is the *why* and *what.* Wayfinder is the *how, when,* and *who.*</p>
    <p>Wayfinder, drawing from the principles of waterfall planning and agile execution, is designed to be adaptable. It can be overlaid on any methodology, giving you the confidence that all critical elements will be addressed.</p>
    <span class="btn">Read More</span>
  </div>
  <div class="photo abs" style="left:623px;top:70px;width:434px;height:375px;background:linear-gradient(135deg,#8a7a6a,#5a4d42)" role="img" aria-label="Video thumbnail of two colleagues talking at a laptop">
    <svg class="abs" style="left:186px;top:128px" width="60" height="60" viewBox="0 0 60 60"><circle cx="30" cy="30" r="30" fill="#f47a20"/><path d="M24 18l18 12-18 12z" fill="#fff"/></svg>
  </div>
</section>

<div class="sec-title abs" style="top:2420px"><span class="mark"></span><h2>OUR SERVICES</h2><span class="rule"></span></div>
<div class="tabs abs">
  <div class="tab active"><span class="dot" style="background:#fff;opacity:.25"></span>Project<br>Planning</div>
  <div class="tab"><span class="dot" style="background:var(--blue)"></span>Project<br>Management</div>
  <div class="tab" style="font-size:13px;line-height:15px"><span class="dot" style="background:#3ec1cf"></span>Project<br>Assessments and<br>Turnaround</div>
  <div class="tab"><span class="dot" style="background:var(--purple)"></span>Change<br>Management</div>
</div>
<div class="photo abs" style="left:150px;top:2755px;width:486px;height:477px;background:linear-gradient(135deg,#c7d0d6,#6d7a86)" role="img" aria-label="Photo of a team planning at a whiteboard"></div>
<div class="service-copy abs">
  <h2>PROJECT<br>PLANNING</h2>
  <div class="quote"><p>"Failing to plan is planning to fail"</p><cite>Edwin Calloway</cite></div>
  <div class="quote"><p>"Everybody has a plan until they get punched in the face"</p><cite>Rex Damon</cite></div>
  <p class="body">Both of these quotes are true, and resolving this paradox is essential to success. I can help you develop a plan based on your current situation and your desired future state.</p>
  <span class="btn" style="margin-top:22px">Read More</span>
</div>

<div class="experience-bg abs"></div>
<div class="sec-title abs" style="top:3342px"><span class="mark"></span><h2>EXPERIENCE</h2><span class="rule"></span></div>
<div class="slide abs" style="left:142px;width:120px;top:3570px;height:290px" role="img" aria-label="Case study photo"></div>
<div class="slide abs" style="left:188px;width:120px;top:3550px;height:330px" role="img" aria-label="Case study photo"></div>
<div class="slide abs" style="left:235px;width:120px;top:3532px;height:366px" role="img" aria-label="Case study photo"></div>
<div class="slide abs" style="left:940px;width:124px;top:3570px;height:290px" role="img" aria-label="Case study photo"></div>
<div class="slide abs" style="left:900px;width:124px;top:3550px;height:330px" role="img" aria-label="Case study photo"></div>
<div class="slide abs" style="left:860px;width:124px;top:3532px;height:366px" role="img" aria-label="Case study photo"></div>
<div class="slide abs" style="left:296px;width:643px;top:3513px;height:402px;background:linear-gradient(90deg,#2c2e33,#6b6d70 60%,#9a9c9f)" role="img" aria-label="Case study photo of colleagues reviewing charts on glass">
  <span class="abs heading" style="left:28px;top:350px;color:#fff;font-size:19px;font-weight:600">Ledgerline</span>
</div>
<span class="btn abs" style="left:535px;top:3954px">Read More</span>
<div class="slider-track abs"></div>
<div class="slider-fill abs"></div>
<div class="slider-knob abs"></div>

<section class="subscribe abs">
  <h2>SUBSCRIBE FOR UPDATES</h2>
</section>
<div class="email-field abs">
  <svg class="abs" style="left:30px;top:19px" width="20" height="15" viewBox="0 0 20 15"><rect width="20" height="15" rx="2" fill="var(--teal)"/><path d="M1 2l9 7 9-7" stroke="#fff" stroke-width="1.6" fill="none"/></svg>
  <span class="email-label">EMAIL ID</span>
  <span class="btn email-submit">SUBSCRIBE</span>
</div>

<footer class="footer abs">
  <div class="footer-logo abs"><span class="brand-dot" style="width:16px;height:16px"></span>COPPER HARBOR ERP<small>BUILT FOR ERP SUCCESS</small></div>
  <div class="f-col abs" style="left:506px"><h4>ERP Tools</h4>Copper Harbor<br>Wayfinder Method<br>Tools and Resources</div>
  <div class="f-col abs" style="left:698px"><h4>Services</h4>About<br>Project Planning<br>Project Management<br>Project Assessment<br>and Turnaround<br>Change Management</div>
  <div class="f-col abs" style="left:898px"><h4>Contact</h4>
    <div class="row"><svg width="12" height="9" viewBox="0 0 12 9"><rect width="12" height="9" fill="#fff"/><path d="M0 0l6 5 6-5" stroke="#1c1c1c" fill="none"/></svg>danmarsh@copperharborerp</div>
    <div class="row"><svg width="12" height="12" viewBox="0 0 12 12"><path d="M2 1l3 0 1 3-2 1a7 7 0 0 0 3 3l1-2 3 1v3C6 11 1 6 2 1z" fill="#fff"/></svg>phone: (555) 014-0287</div>
  </div>
  <p class="copyright abs">Copyright © 2024 All Rights Reserved</p>
</footer>

</body>
</html>
```